Redesign of business card for Cedar Ridge Mechanical

We are looking for a new design for our business cards for Cedar Ridge Mechanical. We are a plumbing & HVAC construction company, operating on the West Coast of Canada and USA. Logo attached.
Industry/Entity Type
Construction - Plumbing & HVAC
Contact Information for Business Card
Name, address, phone numbers, email, website address
Look and feel
Each slider illustrates characteristics of the customer's brand and the style your logo design should communicate.

```html
<!DOCTYPE html>
<html lang="en">
<head>
<meta charset="utf-8">
<title>Cedar Ridge Mechanical – Business Card</title>
<link href="https://fonts.googleapis.com/css2?family=Poppins:wght@300;400;600&display=swap" rel="stylesheet">
<style>
  :root {
    --backdrop: #232323;
    --card: #1d1d20;
    --card-back: #1b1b1e;
    --ink: #ffffff;
    --ink-soft: #d9d9d9;
    --ink-muted: #3a3a3e;
    --rule: #9a9a9a;
  }
  * { margin: 0; padding: 0; box-sizing: border-box; }
  html, body { width: 1200px; height: 780px; overflow: hidden; }
  body {
    background: var(--backdrop);
    font-family: "Poppins", sans-serif;
    color: var(--ink);
    position: relative;
  }
  .card {
    position: absolute;
    top: 235px;
    width: 540px;
    height: 310px;
    border-radius: 4px;
    overflow: hidden;
    box-shadow: 0 18px 40px rgba(0,0,0,.55);
  }
  .card--front { left: 40px; background: var(--card); }
  .card--back { left: 620px; background: var(--card-back); }

  .edge-bar { position: absolute; background: var(--ink); width: 8px; }
  .edge-bar--left { left: 0; top: 0; height: 150px; }
  .edge-bar--right { right: 0; top: 0; height: 170px; }

  .brand {
    position: absolute; left: 44px; top: 62px; width: 200px;
    display: flex; align-items: center; gap: 12px;
  }
  .brand__mark { width: 22px; height: 22px; border: 3px solid var(--ink); border-radius: 3px; flex: none; }
  .brand__name {
    font-weight: 600; font-size: 21px; line-height: 1.15; letter-spacing: .02em; text-transform: uppercase;
  }

  .divider { position: absolute; left: 238px; top: 80px; }

  .contact { position: absolute; left: 300px; top: 74px; }
  .contact__name { font-size: 26px; line-height: 1.1; font-weight: 300; white-space: nowrap; }
  .contact__name strong { font-weight: 600; }
  .contact__role { font-size: 13px; font-weight: 400; margin-top: 2px; color: var(--ink-soft); }
  .contact__list { list-style: none; margin-top: 18px; font-size: 13.5px; font-weight: 400; }
  .contact__list li { display: flex; align-items: center; gap: 9px; height: 22px; }
  .contact__list svg { width: 12px; height: 12px; flex: none; }

  .address {
    position: absolute; left: 44px; bottom: 34px;
    font-size: 12.5px; font-weight: 400; color: var(--ink-soft); letter-spacing: .01em;
  }

  .back-brand {
    position: absolute; inset: 0;
    display: flex; align-items: center; justify-content: center; gap: 18px;
  }
  .back-brand__mark { width: 34px; height: 34px; border: 4px solid var(--ink-muted); border-radius: 4px; }
  .back-brand__name {
    font-weight: 600; font-size: 30px; line-height: 1.15; text-transform: uppercase;
    letter-spacing: .03em; color: var(--ink-muted);
  }
</style>
</head>
<body>
  <section class="card card--front" aria-label="Business card front">
    <span class="edge-bar edge-bar--left"></span>
    <span class="edge-bar edge-bar--right"></span>

    <div class="brand">
      <span class="brand__mark"></span>
      <span class="brand__name">Cedar Ridge<br>Mechanical</span>
    </div>

    <svg class="divider" width="36" height="110" viewBox="0 0 36 110">
      <line x1="36" y1="0" x2="0" y2="110" stroke="var(--rule)" stroke-width="1"/>
    </svg>

    <div class="contact">
      <p class="contact__name"><strong>Marta</strong> Novak</p>
      <p class="contact__role">Founder &amp; CEO</p>
      <ul class="contact__list">
        <li>
          <svg viewBox="0 0 24 24"><path fill="#fff" d="M6.6 10.8a15.1 15.1 0 0 0 6.6 6.6l2.2-2.2c.3-.3.7-.4 1-.2 1.1.4 2.3.6 3.6.6.6 0 1 .4 1 1V20c0 .6-.4 1-1 1C10.6 21 3 13.4 3 4c0-.6.4-1 1-1h3.5c.6 0 1 .4 1 1 0 1.3.2 2.5.6 3.6.1.3 0 .7-.2 1z"/></svg>
          (555) 014-2276
        </li>
        <li>
          <svg viewBox="0 0 24 24"><circle cx="12" cy="12" r="9" fill="none" stroke="#fff" stroke-width="2"/><path d="M3 12h18M12 3c3 3 3 15 0 18M12 3c-3 3-3 15 0 18" fill="none" stroke="#fff" stroke-width="1.5"/></svg>
          info@cedarridgemech.com
        </li>
        <li>
          <svg viewBox="0 0 24 24"><rect x="3" y="6" width="18" height="12" rx="1" fill="none" stroke="#fff" stroke-width="2"/><path d="M3 7l9 6 9-6" fill="none" stroke="#fff" stroke-width="2"/></svg>
          www.cedarridgemech.com
        </li>
      </ul>
    </div>

    <p class="address">418 Alder Way Suite 120 Portland, OR 97205</p>
  </section>

  <section class="card card--back" aria-label="Business card back">
    <div class="back-brand">
      <span class="back-brand__mark"></span>
      <span class="back-brand__name">Cedar Ridge<br>Mechanical</span>
    </div>
  </section>
</body>
</html>
```